Real Estate Company / Capital Needs Cards!

need business cards designed using the logos that were just designed by pixelbarn.

Reason: per designers request deadline extended 1 day…thank you.

Target Market(s)

Investors and clients looking to purchase real estate or invest in the business.

Industry/Entity Type

Business

Requirements
Must have
• two designs - one for the real estate logo and one for the capital logo, similar but slightly different.
Nice to have
• something to make it pop (perhaps on the back)
Should not have
• much color

```html
<!DOCTYPE html>
<html lang="en">
<head>
<meta charset="utf-8">
<title>Marlow Real Estate – Business Cards</title>
<link rel="stylesheet" href="https://fonts.googleapis.com/css2?family=Cinzel:wght@400;600&display=swap">
<style>
  :root {
    --backdrop: #ecebe8;
    --card: #050505;
    --silver: #d9d9d9;
    --ink-light: #f2f2f2;
    --shade: #262626;
  }
  * { box-sizing: border-box; margin: 0; padding: 0; }
  html, body { width: 1200px; height: 499px; overflow: hidden; }
  body {
    background: var(--backdrop);
    font-family: "Cinzel", serif;
    position: relative;
  }
  .card {
    position: absolute;
    top: 100px;
    width: 520px;
    height: 300px;
    background: var(--card);
    border-radius: 30px;
    overflow: hidden;
    box-shadow: 0 10px 26px rgba(0,0,0,.25);
  }
  .card--front { left: 50px; }
  .card--back  { left: 630px; }

  .backdrop-square {
    position: absolute;
    background: var(--shade);
    border-radius: 22px;
  }
  .card--front .backdrop-square { left: 38px; top: 38px; width: 200px; height: 224px; }
  .card--back  .backdrop-square { left: 175px; top: 40px; width: 170px; height: 220px; opacity: .7; }

  .brand {
    position: absolute;
    color: var(--silver);
    font-weight: 400;
    text-align: center;
    line-height: 1;
  }
  .card--front .brand {
    left: 260px; top: 28px;
    display: flex; align-items: center; gap: 10px;
  }
  .brand-square {
    width: 44px; height: 44px;
    background: var(--silver);
    border-radius: 4px;
  }
  .card--front .brand-name { font-size: 34px; letter-spacing: 1px; }
  .card--front .brand-sub  { font-size: 13px; letter-spacing: 3px; margin-top: 3px; }

  .card--back .brand {
    left: 0; right: 0; top: 96px;
  }
  .card--back .brand-name { font-size: 78px; letter-spacing: 3px; }
  .card--back .brand-sub  { font-size: 30px; letter-spacing: 8px; margin-top: 6px; }

  .contact {
    position: absolute;
    left: 262px; top: 130px;
    width: 240px;
    color: var(--ink-light);
    font-size: 14px;
    line-height: 1.45;
  }
  .contact .person { font-size: 18px; margin-bottom: 6px; }
  .contact .address { margin-top: 10px; }
</style>
</head>
<body>
  <section class="card card--front" aria-label="Business card front">
    <div class="backdrop-square"></div>
    <div class="brand">
      <span class="brand-square"></span>
      <div>
        <div class="brand-name">Marlow</div>
        <div class="brand-sub">Real Estate</div>
      </div>
    </div>
    <div class="contact">
      <p class="person">Your Name, Title</p>
      <p>P: 555-014-2273</p>
      <p>F: 555-014-2291</p>
      <p>E: hello@marlowrealestate.com</p>
      <p class="address">Street Name City Name<br>State ZipCode</p>
    </div>
  </section>

  <section class="card card--back" aria-label="Business card back">
    <div class="backdrop-square"></div>
    <div class="brand">
      <div class="brand-name">Marlow</div>
      <div class="brand-sub">Real Estate</div>
    </div>
  </section>
</body>
</html>
```